Veldmark Supplies Business Card

Professional business card that stand out to our potential customers. Front and back with clean modern design

Industry/Entity Type

Oil and gas

Contact Information for Business Card

Name, address, website , office phone and cell number

Requirements
Must have
• Editable files for each employee

```html
<!DOCTYPE html>
<html lang="en">
<head>
<meta charset="utf-8">
<title>Veldmark Supplies Business Card</title>
<link rel="stylesheet" href="https://fonts.googleapis.com/css2?family=Montserrat:wght@400;500;700;800&display=swap">
<style>
  :root {
    --cyan: #0cafd3;
    --red: #ec1f26;
    --white: #ffffff;
    --stage: #3a3a3a;
    --ink-light: #ffffff;
  }
  * { box-sizing: border-box; margin: 0; padding: 0; }
  html, body { width: 1200px; height: 689px; overflow: hidden; }
  body {
    background: var(--stage);
    font-family: "Montserrat", Arial, sans-serif;
    display: flex;
    align-items: center;
    justify-content: center;
    gap: 40px;
  }
  .card {
    position: relative;
    width: 560px;
    height: 320px;
    overflow: hidden;
  }
  .card-front {
    background: var(--cyan);
    display: flex;
    align-items: center;
    justify-content: center;
  }
  .brand {
    display: flex;
    align-items: center;
    gap: 14px;
  }
  .brand-mark {
    width: 26px;
    height: 26px;
    background: var(--red);
  }
  .brand-name {
    font-weight: 800;
    font-size: 30px;
    letter-spacing: 2px;
    text-transform: uppercase;
    color: var(--white);
  }
  .card-back { background: var(--white); }
  .back-art { position: absolute; inset: 0; }
  .back-brand {
    position: absolute;
    left: 36px;
    top: 112px;
  }
  .back-brand .brand-mark {
    width: 18px;
    height: 18px;
    background: var(--cyan);
  }
  .back-brand .brand-name {
    font-size: 19px;
    letter-spacing: 1.5px;
    color: var(--red);
  }
  .contact {
    position: absolute;
    right: 22px;
    top: 96px;
    color: var(--ink-light);
    text-align: right;
    font-size: 12px;
    line-height: 1.45;
  }
  .contact-name { font-weight: 700; font-size: 14px; letter-spacing: 0.5px; }
  .contact-role { font-weight: 400; font-size: 12px; margin-bottom: 10px; }
  .contact-address { margin-bottom: 4px; }
  .contact-line {
    display: flex;
    align-items: center;
    justify-content: flex-end;
    gap: 8px;
  }
  .icon {
    width: 15px;
    height: 15px;
    background: var(--red);
    display: inline-flex;
    align-items: center;
    justify-content: center;
  }
  .icon svg { width: 11px; height: 11px; }
</style>
</head>
<body>
  <section class="card card-front" aria-label="Card front">
    <div class="brand">
      <span class="brand-mark"></span>
      <span class="brand-name">Veldmark Supplies</span>
    </div>
  </section>

  <section class="card card-back" aria-label="Card back">
    <svg class="back-art" viewBox="0 0 560 320" width="560" height="320" aria-hidden="true">
      <path d="M500,0 C420,40 410,170 310,245 C230,300 90,280 0,305 L0,320 L560,320 L560,0 Z" fill="var(--cyan)"/>
      <path d="M478,0 C398,40 388,168 290,240 C210,296 80,272 0,292" fill="none" stroke="var(--red)" stroke-width="9"/>
      <path d="M462,0 C382,38 372,162 276,232 C196,288 70,262 0,280" fill="none" stroke="var(--cyan)" stroke-width="2.5"/>
    </svg>

    <div class="brand back-brand">
      <span class="brand-mark"></span>
      <span class="brand-name">Veldmark Supplies</span>
    </div>

    <div class="contact">
      <p class="contact-name">DALEN ORRICK</p>
      <p class="contact-role">President</p>
      <p class="contact-address">482 Harlow Ave, Ste 100,<br>Midrand, TX 75209</p>
      <p class="contact-line">555-014-2290
        <span class="icon"><svg viewBox="0 0 12 12"><path d="M3 1 L5 3.5 L4 5 C5 7 6 8 7.5 8.5 L9 7.5 L11 9.5 L9.5 11 C5 10.5 1.5 7 1 2.5 Z" fill="#fff"/></svg></span>
      </p>
      <p class="contact-line">000-000-9999
        <span class="icon"><svg viewBox="0 0 12 12"><rect x="3.5" y="1" width="5" height="10" rx="1" fill="none" stroke="#fff" stroke-width="1.2"/><circle cx="6" cy="9.3" r="0.6" fill="#fff"/></svg></span>
      </p>
      <p class="contact-line">info@example-youremail.com
        <span class="icon"><svg viewBox="0 0 12 12"><rect x="1" y="3" width="10" height="6.5" fill="none" stroke="#fff" stroke-width="1.1"/><path d="M1 3 L6 7 L11 3" fill="none" stroke="#fff" stroke-width="1.1"/></svg></span>
      </p>
      <p class="contact-line">www.example-yourwebsite.com
        <span class="icon"><svg viewBox="0 0 12 12"><circle cx="6" cy="6" r="4.6" fill="none" stroke="#fff" stroke-width="1.1"/><ellipse cx="6" cy="6" rx="2" ry="4.6" fill="none" stroke="#fff" stroke-width="1"/><path d="M1.4 6 H10.6" stroke="#fff" stroke-width="1"/></svg></span>
      </p>
    </div>
  </section>
</body>
</html>
```